Canadian Christian Church needs design for new sermon series

A graphic design for our series and an invitation card to invite people to the series. Check design brief for more detailed information. Target audience: young families and young adults. Looking for a creative design that will get people's attention and create interest. See design brief for copy of design purchased for previous series.
Updates
entered Apr 4 incorrectly. Need a week to receive and review designs, and today is Apr 2/19. Thanks!
Target Market(s)
young families and young adults
Colors
Designer to choose colors to be used in the design.
Look and feel

```html
<!DOCTYPE html>
<html lang="en">
<head>
<meta charset="utf-8">
<title>Messy – Sermon Series Invitation Card</title>
<link href="https://fonts.googleapis.com/css2?family=Anton&family=Montserrat:wght@500;700&family=Roboto+Slab:wght@400;700&display=swap" rel="stylesheet">
<style>
  :root {
    --backdrop: #777777;
    --band: #3b302c;
    --gold: #f6c56b;
    --orange: #f7941d;
    --orange-deep: #e8731a;
    --purple: #6b2a8c;
    --ink: #2f2a26;
    --beige: #d8cdb4;
    --beige-light: #e4dbc6;
    --rule: #6d6458;
    --blue: #1f6fc1;
    --white: #ffffff;
    --shirt: #e4e1de;
    --shirt-shade: #c9c5c3;
    --skin: #b87a4c;
    --pages: #e2cfa4;
  }
  * { box-sizing: border-box; margin: 0; padding: 0; }
  html, body { width: 1200px; height: 903px; overflow: hidden; }
  body { background: var(--backdrop); position: relative; font-family: "Montserrat", "Segoe UI", Arial, sans-serif; }

  .card { position: absolute; width: 482px; height: 378px; overflow: hidden; box-shadow: 0 3px 8px rgba(0,0,0,.35); }

  /* Front */
  .card--front { left: 237px; top: 61px; background: var(--band); }
  .front__photo { position: absolute; left: 0; top: 0; width: 482px; height: 320px;
    background:
      radial-gradient(ellipse 46% 22% at 50% 52%, rgba(226,207,164,.95) 0%, rgba(226,207,164,.6) 55%, rgba(226,207,164,0) 100%),
      radial-gradient(ellipse 60% 30% at 50% 70%, rgba(184,122,76,.85) 0%, rgba(184,122,76,.35) 60%, rgba(184,122,76,0) 100%),
      linear-gradient(180deg, var(--shirt) 0%, #d9d3cc 35%, var(--shirt-shade) 78%, #a9a39f 100%); }
  .front__brand { position: absolute; left: 22px; top: 26px; width: 170px; text-align: center; }
  .front__brand-mark { display: block; width: 58px; height: 58px; margin: 0 auto 6px; border-radius: 50%; background: var(--purple); }
  .front__brand-name { font-family: "Roboto Slab", Rockwell, Georgia, serif; font-weight: 400; font-size: 11.5px; color: var(--ink); white-space: nowrap; }
  .front__series { position: absolute; right: 26px; top: 24px; font-family: "Anton", Impact, "Arial Narrow", sans-serif; font-size: 72px; font-weight: 400;
    line-height: 1; letter-spacing: 1px; color: var(--orange); -webkit-text-stroke: 2px var(--purple); }
  .front__tagline { position: absolute; left: 0; bottom: 0; width: 100%; height: 58px; line-height: 58px; text-align: center;
    font-family: "Roboto Slab", Rockwell, Georgia, serif; font-size: 36px; color: var(--gold); white-space: nowrap; }

  /* Back */
  .card--back { left: 582px; top: 470px;
    background: radial-gradient(ellipse at 75% 40%, var(--beige-light) 0%, var(--beige) 55%, #cfc3a7 100%); }
  .back__heading { position: absolute; top: 22px; width: 100%; text-align: center; color: var(--ink); }
  .back__heading-title { font-family: "Roboto Slab", Rockwell, Georgia, serif; font-weight: 700; font-size: 24px; line-height: 30px; white-space: nowrap; }
  .back__heading-time { font-family: "Montserrat", "Segoe UI", Arial, sans-serif; font-weight: 700; font-size: 25px; line-height: 32px; }
  .back__label { position: absolute; left: 26px; font-weight: 700; font-size: 11.5px; color: var(--ink); white-space: nowrap; }
  .back__label--sermons { top: 100px; }
  .back__label--features { top: 254px; }

  .sermons { position: absolute; left: 27px; top: 117px; width: 228px; border-collapse: collapse; font-size: 10.5px; font-weight: 500; color: var(--ink); }
  .sermons td { border: 1px solid var(--rule); height: 16px; padding: 0 6px; white-space: nowrap; line-height: 14px; }
  .sermons td.sermons__date { width: 73px; }

  .features { position: absolute; left: 28px; top: 270px; list-style: none; font-size: 11px; color: #3d3833; }
  .features li { position: relative; padding-left: 14px; line-height: 14.5px; white-space: nowrap; }
  .features li::before { content: ""; position: absolute; left: 0; top: 4px; width: 7px; height: 7px; border-radius: 50%; background: var(--blue); }

  .back__values { position: absolute; left: 288px; top: 108px; width: 174px; height: 168px; border-radius: 50%;
    background: radial-gradient(circle at 50% 50%, var(--beige-light) 0 20%, rgba(247,148,29,.9) 38%, rgba(31,111,193,.85) 62%, rgba(123,42,142,.8) 82%, rgba(216,205,180,0) 100%); }

  .back__footer { position: absolute; left: 0; bottom: 0; width: 100%; height: 52px; background: var(--band); color: var(--white);
    text-align: center; font-size: 9.5px; padding-top: 9px; line-height: 17px; white-space: nowrap; }
</style>
</head>
<body>

<section class="card card--front">
  <div class="front__photo" role="img" aria-label="Photo of two open hands holding an open Bible"></div>
  <div class="front__brand">
    <span class="front__brand-mark"></span>
    <span class="front__brand-name">Maple Grove Family Church</span>
  </div>
  <h1 class="front__series">MESSY</h1>
  <p class="front__tagline">Joining God in the Mess</p>
</section>

<section class="card card--back">
  <div class="back__heading">
    <h2 class="back__heading-title">THE TIME OF THE SERVICES:</h2>
    <p class="back__heading-time">Sundays @ 10:30</p>
  </div>

  <p class="back__label back__label--sermons">Names &amp; Dates of the sermons:</p>
  <table class="sermons">
    <tr><td class="sermons__date">April 28th:</td><td>We Made This Mess</td></tr>
    <tr><td class="sermons__date">May 5th:</td><td>Bless in the Mess</td></tr>
    <tr><td class="sermons__date">May 12th:</td><td>Born into the Mess</td></tr>
    <tr><td class="sermons__date">May 19th:</td><td>Messy Work</td></tr>
    <tr><td class="sermons__date">May 26th:</td><td>Messy Church</td></tr>
    <tr><td class="sermons__date">June 2nd:</td><td>Messy Hospitality</td></tr>
    <tr><td class="sermons__date">June 9th:</td><td>TBD</td></tr>
    <tr><td class="sermons__date">June 16th:</td><td>Messy within Boundaries</td></tr>
  </table>

  <div class="back__values" role="img" aria-label="Core values ribbon diagram: Equipping, Serving, Missional Living, Spirit-Living, Belonging"></div>

  <p class="back__label back__label--features">Features of the service:</p>
  <ul class="features">
    <li>Staffed nursery &amp; children’s program every Sunday</li>
    <li>Coffee &amp; snacks</li>
    <li>Everyone welcome</li>
  </ul>

  <footer class="back__footer">
    Location - 1180 Cedar Line East Brampton, ON L6X 2B4<br>
    Phone-905-555-0147 | Email-hello@mgfamilychurch.ca | Website-www.mgfamilychurch.ca
  </footer>
</section>

</body>
</html>
```